Pet Sitting Business Card

Would like a business card designed for my new pet sitting business
Card needs to match with logo design.
Blue and Orange are the theme colours.

Simple yet sophisticated design

company name:- MEADOWLARK PET CARE
Dana Kovich
Owner
0452716093
dana@meadowlarkpetcare.com.au
www.meadowlarkpetcare.com.au

I'm going to close my deadline early. I will be picking a winner by the 10th of May. Please submit designs before then.
thank you

Target Market(s)

All types of professional pet lovers wishing to have their pet looked after

Industry/Entity Type

Pet

Requirements
Must have
• Logo design
Blue and orange

```html
<!DOCTYPE html>
<html lang="en">
<head>
<meta charset="utf-8">
<title>Meadowlark Pet Care – Business Card</title>
<link rel="stylesheet" href="https://fonts.googleapis.com/css2?family=Exo+2:wght@400;600;700&display=swap">
<style>
  :root {
    --backdrop: #2e2f31;
    --card: #ffffff;
    --blue: #2f86e0;
    --blue-deep: #1f6fd1;
    --cyan: #62cbe6;
    --orange: #f08a24;
    --ink: #2a2a2a;
    --muted: #4a4a4a;
  }
  * { box-sizing: border-box; margin: 0; padding: 0; }
  html, body { width: 1200px; height: 720px; overflow: hidden; }
  body {
    background: var(--backdrop);
    font-family: "Exo 2", sans-serif;
    position: relative;
  }
  .card {
    position: absolute;
    width: 500px;
    height: 290px;
    top: 215px;
    background: var(--card);
    border-radius: 22px;
    overflow: hidden;
    box-shadow: 0 14px 30px rgba(0,0,0,.35);
  }
  .card--front { left: 70px; }
  .card--back { left: 630px; }
  .swoosh { position: absolute; inset: 0; width: 100%; height: 100%; }

  .brand {
    position: absolute;
    text-align: center;
    color: var(--blue-deep);
    font-weight: 700;
    letter-spacing: 1px;
    line-height: 1.05;
  }
  .brand__dot {
    display: block;
    margin: 0 auto 8px;
    width: 26px; height: 26px;
    border-radius: 50%;
    background: var(--orange);
  }
  .brand__name { font-size: 34px; display: block; }
  .brand__sub { font-size: 22px; display: block; letter-spacing: 3px; }
  .card--front .brand { left: 0; right: 0; top: 100px; }
  .card--back .brand { right: 26px; top: 66px; }
  .card--back .brand__name { font-size: 28px; }
  .card--back .brand__sub { font-size: 18px; }
  .card--back .brand__dot { width: 22px; height: 22px; }

  .person {
    position: absolute;
    right: 28px;
    top: 178px;
    text-align: right;
  }
  .person__name {
    font-size: 16px;
    font-weight: 600;
    letter-spacing: 1.5px;
    color: var(--blue);
  }
  .person__role {
    font-size: 12px;
    letter-spacing: 1px;
    color: var(--ink);
  }

  .contacts {
    position: absolute;
    left: 22px;
    bottom: 18px;
    list-style: none;
  }
  .contacts li {
    display: flex;
    align-items: center;
    gap: 7px;
    font-size: 11px;
    color: var(--muted);
    height: 17px;
  }
  .contacts svg { width: 13px; height: 13px; flex: none; }
</style>
</head>
<body>

<section class="card card--front" aria-label="Card front">
  <svg class="swoosh" viewBox="0 0 500 290" preserveAspectRatio="none" aria-hidden="true">
    <defs>
      <linearGradient id="frontBlue" x1="0" x2="1" y1="0" y2="0">
        <stop offset="0" stop-color="#2f86e0"/>
        <stop offset=".5" stop-color="#62cbe6"/>
        <stop offset="1" stop-color="#2f86e0"/>
      </linearGradient>
    </defs>
    <path d="M0 0 H500 V14 C360 14 150 40 0 118 Z" fill="url(#frontBlue)"/>
  </svg>
  <div class="brand">
    <span class="brand__dot"></span>
    <span class="brand__name">MEADOWLARK</span>
    <span class="brand__sub">PET CARE</span>
  </div>
</section>

<section class="card card--back" aria-label="Card back">
  <svg class="swoosh" viewBox="0 0 500 290" preserveAspectRatio="none" aria-hidden="true">
    <defs>
      <linearGradient id="backBlue" x1="0" x2="1" y1="0" y2="0">
        <stop offset="0" stop-color="#2f86e0"/>
        <stop offset=".45" stop-color="#62cbe6"/>
        <stop offset="1" stop-color="#2f86e0"/>
      </linearGradient>
    </defs>
    <path d="M0 0 H500 V12 C340 14 150 40 0 122 Z" fill="url(#backBlue)"/>
    <path d="M0 132 C150 50 340 22 500 20" fill="none" stroke="var(--orange)" stroke-width="4"/>
  </svg>

  <div class="brand">
    <span class="brand__dot"></span>
    <span class="brand__name">MEADOWLARK</span>
    <span class="brand__sub">PET CARE</span>
  </div>

  <div class="person">
    <p class="person__name">DANA KOVICH</p>
    <p class="person__role">FINANCIAL ADVISOR</p>
  </div>

  <ul class="contacts">
    <li>
      <svg viewBox="0 0 16 16" aria-hidden="true"><circle cx="8" cy="8" r="8" fill="var(--blue)"/><path d="M5.2 4.2l1.6-.2.8 2-1 .8a6 6 0 0 0 2.6 2.6l.8-1 2 .8-.2 1.6c-3.4.4-6.8-3-6.6-6.6z" fill="#fff"/></svg>
      045 271 6093
    </li>
    <li>
      <svg viewBox="0 0 16 16" aria-hidden="true"><circle cx="8" cy="8" r="8" fill="var(--blue)"/><path d="M5.2 4.2l1.6-.2.8 2-1 .8a6 6 0 0 0 2.6 2.6l.8-1 2 .8-.2 1.6c-3.4.4-6.8-3-6.6-6.6z" fill="#fff"/></svg>
      045 271 6093
    </li>
    <li>
      <svg viewBox="0 0 16 16" aria-hidden="true"><circle cx="8" cy="8" r="8" fill="var(--blue)"/><rect x="4" y="5.2" width="8" height="5.6" rx=".6" fill="#fff"/><path d="M4.3 5.6L8 8.4l3.7-2.8" fill="none" stroke="var(--blue)" stroke-width=".9"/></svg>
      dana@meadowlarkpetcare.com.au
    </li>
    <li>
      <svg viewBox="0 0 16 16" aria-hidden="true"><circle cx="8" cy="8" r="8" fill="var(--blue)"/><circle cx="8" cy="8" r="4" fill="none" stroke="#fff" stroke-width="1"/><path d="M4 8h8M8 4c-2 2.4-2 5.6 0 8M8 4c2 2.4 2 5.6 0 8" fill="none" stroke="#fff" stroke-width=".8"/></svg>
      www.meadowlarkpetcare.com.au
    </li>
    <li>
      <svg viewBox="0 0 16 16" aria-hidden="true"><circle cx="8" cy="8" r="8" fill="var(--blue)"/><path d="M8 3.6a3 3 0 0 0-3 3c0 2.2 3 5.8 3 5.8s3-3.6 3-5.8a3 3 0 0 0-3-3z" fill="#fff"/><circle cx="8" cy="6.6" r="1.1" fill="var(--blue)"/></svg>
      12 Wattle Lane, Brookfield QLD
    </li>
  </ul>
</section>

</body>
</html>
```